Landing Page and Logo for Auto-Blogging Platform

I created a platform that allows users to start a blog for their business, hobby, charity, etc. I need a landing page where users can learn about the platform, benefits of consistent blogging, SEO value, plans/pricing, etc. The landing page needs to have multiple call to action buttons encouraging the visitor to register/sign up for a free trial.

In addition to the landing page, I need a page for users to establish the settings for their blog. This page should be a fairly simple form, intended for the user to enter a few details to set up their blog:
1. Name of Blog
2. Up to 10 topics and/or keywords the blog should focus on
3. Theme: Color-scheme and logo upload for blog.

I have attached the specifications of the platform's functionality so you can better understand how it works, plans/pricing, etc.

I also need a logo for the business. The name of the platform is PostNook.

Target Market(s)

Website owners, bloggers, business owners

Industry/Entity Type

Technology, Internet, web design

Coding

Coded - Design and coding required

Number of Pages Required

2 page

Colors
0054AA
0677BA
7BADD7
CADEEF
E8F1F8
0094D4
00A9DD
6FCCEA
C7EBF8
E9F6FB

Requirements
Must have
• Eye-catching design but fairly light on content (keep it simple and brief.)
Nice to have
• Eye-catching yet simple design, clean and easy to understand what we are offering.
Should not have
• Too much “wordy” and confusing content.

```html
<!DOCTYPE html>
<html lang="en">
<head>
<meta charset="utf-8">
<title>PostNook – Auto-Blogging Platform</title>
<link href="https://fonts.googleapis.com/css2?family=Montserrat:wght@300;400;600;700&family=Roboto:wght@300;400;500;700&display=swap" rel="stylesheet">
<style>
:root{
  --blue-dark:#0054AA;
  --blue:#0677BA;
  --blue-mid:#7BADD7;
  --blue-pale:#CADEEF;
  --blue-mist:#E8F1F8;
  --sky:#0094D4;
  --sky-2:#00A9DD;
  --sky-3:#6FCCEA;
  --sky-pale:#C7EBF8;
  --sky-mist:#E9F6FB;
  --ink:#111418;
  --text:#555b62;
  --white:#ffffff;
}
*{box-sizing:border-box;margin:0;padding:0}
html,body{width:1200px;height:3347px;overflow:hidden}
body{font-family:'Roboto',sans-serif;color:var(--ink);background:var(--white);position:relative}
.abs{position:absolute}
.btn{position:absolute;display:flex;align-items:center;justify-content:center;border-radius:20px;background:var(--blue-dark);color:var(--white);font-size:15px;font-family:'Roboto',sans-serif;text-decoration:none}
.heading{font-family:'Montserrat',sans-serif;font-size:38px;letter-spacing:.5px;color:var(--ink)}
.heading b{font-weight:700}
.heading span{font-weight:300;color:var(--blue-dark)}
.underline{position:absolute;height:4px;width:68px;background:var(--blue-dark)}

/* header */
.site-header{position:absolute;top:0;left:0;width:1200px;height:70px;background:var(--white)}
.brand{position:absolute;left:112px;top:14px;display:flex;align-items:center;gap:12px}
.brand-dot{width:40px;height:40px;border-radius:50%;background:var(--blue-dark)}
.brand-name{font-family:'Montserrat',sans-serif;font-weight:700;font-size:30px;color:var(--blue-dark)}
.nav a{position:absolute;top:27px;font-size:15px;font-weight:500;color:var(--ink);text-decoration:none}
.nav a.active{color:var(--blue-dark)}

/* hero */
.hero{position:absolute;top:70px;left:0;width:1200px;height:555px;overflow:hidden}
.hero-photo{position:absolute;inset:0;background:linear-gradient(100deg,#f3f4f3 0%,#e6e8e7 35%,#c9ced0 60%,#a9b3b8 80%,#8f9aa0 100%)}
.hero-copy{position:absolute;left:112px;top:148px}
.hero-welcome{font-size:20px;font-weight:400;letter-spacing:.5px}
.hero-title{font-family:'Montserrat',sans-serif;font-weight:600;font-size:68px;line-height:1;margin-top:20px;color:var(--ink)}
.hero-text{font-size:16px;font-weight:400;line-height:21px;margin-top:14px;width:360px;color:#222}

/* about */
.about{position:absolute;top:625px;left:0;width:1200px;height:527px}
.about p{position:absolute;left:112px;width:450px;font-size:15px;line-height:26px;color:var(--text)}
.dots{position:absolute;left:609px;top:68px;width:130px;height:98px;background-image:radial-gradient(circle,#777 1.2px,transparent 1.6px);background-size:13px 13px}
.about-frame{position:absolute;left:700px;top:129px;width:388px;height:318px;border:2px solid var(--blue-dark);border-radius:3px}
.about-photo{position:absolute;left:642px;top:84px;width:438px;height:355px;background:linear-gradient(120deg,#e9ecec 0%,#d8dedd 40%,#5f87ad 70%,#3a5e86 100%)}

/* benefits */
.benefits{position:absolute;top:1152px;left:0;width:1200px;height:595px;overflow:hidden;background:linear-gradient(135deg,#0a5fb0 0%,var(--blue-dark) 50%,#0a6bbf 100%)}
.benefits .heading{color:var(--white)}
.benefits .heading span{color:var(--white)}
.benefit-label{position:absolute;color:var(--white);font-size:20px;font-weight:500;line-height:25px}

/* pricing */
.pricing{position:absolute;top:1747px;left:0;width:1200px;height:747px}
.plan{position:absolute;background:var(--white);border-radius:12px;box-shadow:0 4px 18px rgba(0,40,90,.12);overflow:hidden}
.plan-head{position:absolute;left:0;top:0;width:100%;height:190px}
.plan-info{position:absolute;left:0;width:100%;text-align:center;color:var(--white)}
.plan-name{font-size:27px;font-weight:700;letter-spacing:.3px;line-height:32px}
.plan-price,.plan-period{font-size:26px;font-weight:400;line-height:32px;margin-top:6px}
.features{position:absolute;list-style:none}
.features li{display:flex;align-items:center;gap:10px;font-size:15.5px;color:var(--text);height:20px}
.premium .features li{color:var(--white)}

/* methods */
.methods{position:absolute;top:2494px;left:0;width:1200px;height:514px;background:linear-gradient(160deg,#e9f3fb 0%,#dbeaf6 60%,#d3e5f4 100%)}
.step-text{position:absolute;text-align:center;font-size:15px;line-height:25.5px;color:#333}
.step-art{position:absolute;border-radius:10px;background:linear-gradient(135deg,var(--sky-pale),var(--blue-mid))}

/* footer */
.site-footer{position:absolute;top:3008px;left:0;width:1200px;height:339px;background:var(--blue-dark);color:var(--white)}
.footer-brand{position:absolute;left:112px;top:64px;display:flex;align-items:center;gap:14px}
.footer-brand .brand-dot{background:var(--white);width:44px;height:44px}
.footer-brand .brand-name{color:var(--white);font-size:40px;font-weight:600}
.footer-about{position:absolute;left:112px;top:142px;width:380px;font-size:15px;line-height:26px}
.footer-title{position:absolute;top:63px;font-size:18px;font-weight:500}
.footer-links a{position:absolute;left:533px;color:var(--white);font-size:15px;text-decoration:none}
.contact-item{position:absolute;left:710px;display:flex;align-items:center;gap:14px}
.contact-icon{width:42px;height:42px;border-radius:50%;background:var(--white);display:flex;align-items:center;justify-content:center}
.contact-item small{display:block;font-size:12.5px;font-weight:700}
.contact-item span{font-size:15px}
.social{position:absolute;top:110px;width:32px;height:32px;border-radius:50%;border:2px solid var(--white)}
.copyright{position:absolute;left:0;top:304px;width:1200px;text-align:center;font-size:15px}
</style>
</head>
<body>

<header class="site-header">
  <div class="brand"><div class="brand-dot"></div><div class="brand-name">PostNook</div></div>
  <nav class="nav">
    <a class="active" style="left:442px">HOME</a>
    <a style="left:521px">ABOUT US</a>
    <a style="left:629px">METHODS</a>
    <a style="left:736px">PRICING</a>
    <a style="left:831px">BENEFITS</a>
  </nav>
  <a class="btn" style="left:968px;top:14px;width:120px;height:38px">CONTACT US</a>
</header>

<section class="hero">
  <div class="hero-photo" role="img" aria-label="Photo of a man in glasses working on a laptop at a bright desk"></div>
  <div class="hero-copy">
    <div class="hero-welcome">WELCOME TO</div>
    <div class="hero-title">POSTNOOK</div>
    <p class="hero-text">Lorem ipsum dolor sit amet, consectetur cng it,<br>sed do&nbsp; incididunt dolore magna aliqua.</p>
  </div>
  <a class="btn" style="left:112px;top:325px;width:218px;height:37px">SIGN UP FOR A FREE TRAIL</a>
</section>

<section class="about">
  <h2 class="heading abs" style="left:112px;top:80px"><b>ABOUT</b> <span>US</span></h2>
  <div class="underline" style="left:112px;top:129px"></div>
  <p style="top:168px">The purpose of this platform is to allow anyone to start a blog and automate the process of creating content and posting it to the blog.</p>
  <p style="top:254px">Lorem ipsum dolor sit amet, consectetur adipiscing elit, sed do eiusmod tempor incididunt ut labore et dolore magna aliqua. Ut enim ad minim veniam, quis nostrud exercitation ullamco laboris nisi ut aliquip ex ea commodo consequat. Duis aute irure dolor in reprehenderit in voluptate velitpariatur.</p>
  <a class="btn" style="left:112px;top:400px;width:115px;height:37px">READ MORE</a>
  <div class="dots"></div>
  <div class="about-frame"></div>
  <div class="about-photo" role="img" aria-label="Photo of a smiling woman in a denim jacket typing on a laptop"></div>
</section>

<section class="benefits">
  <svg class="abs" style="left:0;top:0" width="1200" height="595" viewBox="0 0 1200 595">
    <g stroke="rgba(255,255,255,.12)" stroke-width="1" fill="none">
      <path d="M900 40 L1020 110 L1110 60 L1200 140 M1020 110 L980 230 L1090 260 L1200 210 M980 230 L880 330 L960 420 L1090 260"/>
      <path d="M0 520 L90 460 L150 560 M90 460 L60 380"/>
    </g>
    <circle cx="592" cy="535" r="281" fill="none" stroke="rgba(255,255,255,.35)" stroke-dasharray="3 4"/>
    <circle cx="592" cy="535" r="229" fill="none" stroke="#fff" stroke-width="8"/>
    <circle cx="592" cy="535" r="209" fill="var(--sky-pale)"/>
    <g>
      <circle cx="592" cy="254" r="38" fill="rgba(255,255,255,.25)"/><circle cx="592" cy="254" r="29" fill="var(--sky-mist)"/>
      <rect x="577" y="241" width="30" height="26" rx="2" fill="none" stroke="#222" stroke-width="2"/><line x1="577" y1="248" x2="607" y2="248" stroke="#222" stroke-width="2"/><circle cx="594" cy="258" r="5" fill="none" stroke="#222" stroke-width="2"/>
      <circle cx="377" cy="356" r="38" fill="rgba(255,255,255,.25)"/><circle cx="377" cy="356" r="29" fill="var(--sky-mist)"/>
      <rect x="362" y="343" width="30" height="26" rx="2" fill="none" stroke="#222" stroke-width="2"/><line x1="362" y1="350" x2="392" y2="350" stroke="#222" stroke-width="2"/><line x1="367" y1="360" x2="387" y2="360" stroke="#222" stroke-width="2"/>
      <circle cx="783" cy="334" r="38" fill="rgba(255,255,255,.25)"/><circle cx="783" cy="334" r="29" fill="var(--sky-mist)"/>
      <rect x="768" y="320" width="30" height="21" rx="2" fill="none" stroke="#222" stroke-width="2"/><line x1="783" y1="341" x2="783" y2="349" stroke="#222" stroke-width="2"/><line x1="774" y1="349" x2="792" y2="349" stroke="#222" stroke-width="2"/>
      <circle cx="317" cy="494" r="38" fill="rgba(255,255,255,.25)"/><circle cx="317" cy="494" r="29" fill="var(--sky-mist)"/>
      <rect x="302" y="483" width="26" height="22" rx="2" fill="none" stroke="#222" stroke-width="2"/><line x1="315" y1="492" x2="332" y2="476" stroke="#222" stroke-width="2"/>
      <circle cx="861" cy="494" r="38" fill="rgba(255,255,255,.25)"/><circle cx="861" cy="494" r="29" fill="var(--sky-mist)"/>
      <rect x="846" y="481" width="30" height="26" rx="2" fill="none" stroke="#222" stroke-width="2"/><rect x="851" y="487" width="8" height="8" fill="none" stroke="#222" stroke-width="1.5"/><line x1="863" y1="489" x2="872" y2="489" stroke="#222" stroke-width="1.5"/><line x1="851" y1="500" x2="872" y2="500" stroke="#222" stroke-width="1.5"/>
    </g>
    <circle cx="592" cy="455" r="26" fill="var(--blue-dark)"/>
    <text x="592" y="545" text-anchor="middle" font-family="Montserrat, sans-serif" font-weight="700" font-size="48" fill="#111418">POSTNOOK</text>
  </svg>
  <h2 class="heading abs" style="left:0;width:1200px;text-align:center;top:55px"><b>OUR</b> <span>BENIFITS</span></h2>
  <div class="underline" style="left:562px;top:105px;background:#fff"></div>
  <div class="benefit-label" style="left:442px;width:300px;text-align:center;top:162px">Lorem ipsum dolor sit<br>amet, consectetur</div>
  <div class="benefit-label" style="left:29px;width:300px;text-align:right;top:325px">Lorem ipsum dolor sit<br>amet, consectetur</div>
  <div class="benefit-label" style="left:836px;top:306px">Lorem ipsum dolor sit<br>amet, consectetur</div>
  <div class="benefit-label" style="left:0;width:266px;text-align:right;top:475px">Lorem ipsum dolor sit<br>amet, consectetur</div>
  <div class="benefit-label" style="left:910px;top:468px">Lorem ipsum dolor sit<br>amet, consectetur</div>
</section>

<section class="pricing">
  <h2 class="heading abs" style="left:0;width:1200px;text-align:center;top:80px"><b>OUR</b> <span>PRICING</span></h2>
  <div class="underline" style="left:566px;top:139px"></div>

  <article class="plan" style="left:113px;top:226px;width:294px;height:433px">
    <svg class="plan-head" viewBox="0 0 294 190" preserveAspectRatio="none"><path d="M0 0H294V166C255 170 220 146 150 150C85 154 45 186 0 188Z" fill="var(--blue-dark)"/></svg>
    <div class="plan-info" style="top:22px"><div class="plan-name">BASE PLAN</div><div class="plan-price">$9.99/mo</div><div class="plan-period">Every Month</div></div>
    <ul class="features" style="left:30px;top:206px">
      <li><svg width="20" height="20"><circle cx="10" cy="10" r="10" fill="var(--blue)"/><path d="M5 10l3.5 3.5L15 7" stroke="#fff" stroke-width="2.2" fill="none"/></svg>Lorem ipsum dolor sit amet</li>
      <li style="margin-top:17px"><svg width="20" height="20"><circle cx="10" cy="10" r="10" fill="var(--blue)"/><path d="M5 10l3.5 3.5L15 7" stroke="#fff" stroke-width="2.2" fill="none"/></svg>Lorem ipsum dolor sit amet</li>
      <li style="margin-top:17px"><svg width="20" height="20"><circle cx="10" cy="10" r="10" fill="var(--blue)"/><path d="M5 10l3.5 3.5L15 7" stroke="#fff" stroke-width="2.2" fill="none"/></svg>Lorem ipsum dolor sit amet</li>
      <li style="margin-top:17px"><svg width="20" height="20"><circle cx="10" cy="10" r="10" fill="var(--blue)"/><path d="M5 10l3.5 3.5L15 7" stroke="#fff" stroke-width="2.2" fill="none"/></svg>Lorem ipsum dolor sit amet</li>
    </ul>
    <a class="btn" style="left:30px;top:358px;width:116px;height:38px">READ MORE</a>
  </article>

  <article class="plan premium" style="left:450px;top:201px;width:301px;height:458px;background:var(--blue-dark)">
    <svg class="plan-head" style="height:210px" viewBox="0 0 301 210" preserveAspectRatio="none"><defs><linearGradient id="premiumTop" x1="0" y1="0" x2="0" y2="1"><stop offset="0" stop-color="var(--sky)"/><stop offset="1" stop-color="var(--blue)"/></linearGradient></defs><path d="M0 0H301V200C270 170 230 196 180 186C120 174 60 162 0 186Z" fill="url(#premiumTop)"/></svg>
    <div class="plan-info" style="top:30px"><div class="plan-name">PREMIUM PLAN</div><div class="plan-price">$14.99/mo</div><div class="plan-period">Every Week</div></div>
    <ul class="features" style="left:38px;top:232px">
      <li><svg width="22" height="22"><circle cx="11" cy="11" r="11" fill="#fff"/><path d="M6 11l3.5 3.5L16 8" stroke="var(--blue-dark)" stroke-width="2.2" fill="none"/></svg>Lorem ipsum dolor sit amet</li>
      <li style="margin-top:21px"><svg width="22" height="22"><circle cx="11" cy="11" r="11" fill="#fff"/><path d="M6 11l3.5 3.5L16 8" stroke="var(--blue-dark)" stroke-width="2.2" fill="none"/></svg>Lorem ipsum dolor sit amet</li>
      <li style="margin-top:21px"><svg width="22" height="22"><circle cx="11" cy="11" r="11" fill="#fff"/><path d="M6 11l3.5 3.5L16 8" stroke="var(--blue-dark)" stroke-width="2.2" fill="none"/></svg>Lorem ipsum dolor sit amet</li>
      <li style="margin-top:21px"><svg width="22" height="22"><circle cx="11" cy="11" r="11" fill="#fff"/><path d="M6 11l3.5 3.5L16 8" stroke="var(--blue-dark)" stroke-width="2.2" fill="none"/></svg>Lorem ipsum dolor sit amet</li>
    </ul>
    <a class="btn" style="left:39px;top:399px;width:117px;height:38px;background:#fff;color:#222">READ MORE</a>
  </article>

  <article class="plan" style="left:794px;top:226px;width:294px;height:433px">
    <svg class="plan-head" viewBox="0 0 294 190" preserveAspectRatio="none"><path d="M0 0H294V166C255 170 220 146 150 150C85 154 45 186 0 188Z" fill="var(--blue-dark)"/></svg>
    <div class="plan-info" style="top:26px"><div class="plan-name">ULTIMATE PLAN</div><div class="plan-price">$24.99/mo</div><div class="plan-period">Per Day</div></div>
    <ul class="features" style="left:31px;top:206px">
      <li><svg width="20" height="20"><circle cx="10" cy="10" r="10" fill="var(--blue)"/><path d="M5 10l3.5 3.5L15 7" stroke="#fff" stroke-width="2.2" fill="none"/></svg>Lorem ipsum dolor sit amet</li>
      <li style="margin-top:17px"><svg width="20" height="20"><circle cx="10" cy="10" r="10" fill="var(--blue)"/><path d="M5 10l3.5 3.5L15 7" stroke="#fff" stroke-width="2.2" fill="none"/></svg>Lorem ipsum dolor sit amet</li>
      <li style="margin-top:17px"><svg width="20" height="20"><circle cx="10" cy="10" r="10" fill="var(--blue)"/><path d="M5 10l3.5 3.5L15 7" stroke="#fff" stroke-width="2.2" fill="none"/></svg>Lorem ipsum dolor sit amet</li>
      <li style="margin-top:17px"><svg width="20" height="20"><circle cx="10" cy="10" r="10" fill="var(--blue)"/><path d="M5 10l3.5 3.5L15 7" stroke="#fff" stroke-width="2.2" fill="none"/></svg>Lorem ipsum dolor sit amet</li>
    </ul>
    <a class="btn" style="left:29px;top:358px;width:116px;height:38px">READ MORE</a>
  </article>
</section>

<section class="methods">
  <h2 class="heading abs" style="left:0;width:1200px;text-align:center;top:52px"><b>BLOG TOPICS</b>&nbsp; <span>METHODS</span></h2>
  <div class="underline" style="left:566px;top:110px"></div>
  <svg class="abs" style="left:0;top:0" width="1200" height="514" viewBox="0 0 1200 514">
    <g fill="var(--blue-dark)">
      <circle cx="264" cy="313" r="137"/><path d="M392 290 L420 313 L392 336Z"/>
      <circle cx="599" cy="313" r="137"/><path d="M727 290 L755 313 L727 336Z"/>
      <circle cx="932" cy="313" r="137"/><path d="M1060 290 L1088 313 L1060 336Z"/>
    </g>
    <g fill="#fff">
      <circle cx="249" cy="313" r="135"/>
      <circle cx="584" cy="313" r="135"/>
      <circle cx="917" cy="313" r="135"/>
    </g>
  </svg>
  <div class="step-art" style="left:214px;top:255px;width:68px;height:68px" role="img" aria-label="Illustration of a person typing on a laptop"></div>
  <div class="step-text" style="left:134px;top:333px;width:230px;color:#666">The user enters them into a<br>table manually.</div>
  <div class="step-art" style="left:548px;top:218px;width:72px;height:72px" role="img" aria-label="Illustration of an AI processor chip"></div>
  <div class="step-text" style="left:464px;top:298px;width:240px">AI can create the list of blog<br>topics based on a prompt<br>such as:Provide a list of 52 blog<br>topics for a handyman<br>business's blog</div>
  <div class="step-art" style="left:883px;top:238px;width:70px;height:70px" role="img" aria-label="Illustration of a document with an upload arrow"></div>
  <div class="step-text" style="left:802px;top:316px;width:230px">The user uploads a list of blog<br>topics in CSV format.</div>
</section>

<footer class="site-footer">
  <div class="footer-brand"><div class="brand-dot"></div><div class="brand-name">PostNook</div></div>
  <p class="footer-about">Lorem ipsum dolor sit amet, consectetur adipiscing elit, sed do eiusmod tempor incididunt ut labore et dolore magna aliqua. Quis ipsum suspendisse ltrices gravida. Risus commodo viverra maecenas acus vel facilisis.</p>

  <div class="footer-title" style="left:530px">QUICK LINKS</div>
  <nav class="footer-links">
    <a style="top:99px;font-weight:700">Home</a>
    <a style="top:138px">About Us</a>
    <a style="top:177px">Methods</a>
    <a style="top:216px">Pricing</a>
    <a style="top:255px">Benefits</a>
  </nav>

  <div class="footer-title" style="left:708px">CONTACT US</div>
  <div class="contact-item" style="top:100px">
    <div class="contact-icon"><svg width="20" height="16"><rect x="1" y="1" width="18" height="14" rx="2" fill="var(--blue-dark)"/><path d="M1 2l9 7 9-7" stroke="#fff" stroke-width="1.6" fill="none"/></svg></div>
    <div><small>EMAIL:</small><span>info@postnook.com</span></div>
  </div>
  <div class="contact-item" style="top:164px">
    <div class="contact-icon"><svg width="18" height="18" viewBox="0 0 24 24"><path d="M6.6 10.8a15 15 0 006.6 6.6l2.2-2.2a1 1 0 011-.25 11.4 11.4 0 003.6.57 1 1 0 011 1V20a1 1 0 01-1 1A17 17 0 013 4a1 1 0 011-1h3.5a1 1 0 011 1c0 1.250.2 2.450.57 3.57a1 1 0 01-.25 1z" fill="var(--blue-dark)"/></svg></div>
    <div><small>PHONE NO:</small><span>+1(555) 010 2040</span></div>
  </div>
  <div class="contact-item" style="top:231px">
    <div class="contact-icon"><svg width="18" height="22" viewBox="0 0 18 22"><path d="M9 0a8 8 0 00-8 8c0 6 8 14 8 14s8-8 8-14a8 8 0 00-8-8z" fill="var(--blue-dark)"/><circle cx="9" cy="8" r="3" fill="#fff"/></svg></div>
    <div><small>LOCATION:</small><span>PostNook, USA</span></div>
  </div>

  <div class="footer-title" style="left:984px">FOLLOW US</div>
  <div class="social" style="left:974px"></div>
  <div class="social" style="left:1015px"></div>
  <div class="social" style="left:1056px"></div>

  <div class="copyright">Copyright © 2024 PostNook all rights reserved.</div>
</footer>

</body>
</html>
```